Corvane Freight Company Business Card Design

We are a company that delivers natural saltwater (from the ocean) to aquarium companies, restaurants and home marine tanks. I would like a new business card to suit.

Must include Name, company name, abn, contact number and website as well as logo (see attached).

Looking for a design that stands out, has a clean but unique appearance.

Double and single sided entries welcome

Business

• Logo

```html
<!DOCTYPE html>
<html lang="en">
<head>
<meta charset="utf-8">
<title>Corvane Freight Company Business Card</title>
<link rel="stylesheet" href="https://fonts.googleapis.com/css2?family=Open+Sans:wght@400;600;700&display=swap">
<style>
  :root {
    --backdrop: #2a2a2a;
    --card-blue: #3170e6;
    --card-blue-deep: #1f55c4;
    --aqua: #a8dcf5;
    --white: #ffffff;
  }
  * { margin: 0; padding: 0; box-sizing: border-box; }
  html, body {
    width: 1200px;
    height: 1017px;
    overflow: hidden;
    background: var(--backdrop);
    font-family: "Open Sans", Arial, sans-serif;
    color: var(--white);
  }
  .canvas { position: relative; width: 1200px; height: 1017px; }
  .card {
    position: absolute;
    width: 744px;
    height: 424px;
    background: var(--card-blue);
    overflow: hidden;
  }
  .card--front { left: 81px; top: 54px; }
  .card--back { left: 394px; top: 528px; }

  .holder {
    position: absolute;
    top: 10px;
    left: 0;
    width: 100%;
    text-align: center;
    font-size: 25px;
    font-weight: 400;
  }
  .holder__name { font-weight: 700; }

  .wordmark {
    position: absolute;
    left: 0;
    width: 100%;
    text-align: center;
    font-size: 58px;
    font-weight: 700;
    line-height: 1;
    letter-spacing: -0.5px;
    color: var(--white);
  }
  .card--front .wordmark { top: 128px; }
  .card--back .wordmark { top: 170px; }

  .address {
    position: absolute;
    right: 398px;
    top: 286px;
    text-align: right;
    font-size: 17px;
    line-height: 26px;
  }
  .address__company { font-size: 19px; }
  .divider {
    position: absolute;
    left: 368px;
    top: 282px;
    width: 2px;
    height: 84px;
    background: var(--white);
    opacity: 0.85;
  }
  .contact {
    position: absolute;
    left: 384px;
    top: 284px;
    list-style: none;
    font-size: 18px;
    line-height: 26px;
  }
  .contact li { display: flex; align-items: center; gap: 6px; }
  .contact svg { width: 14px; height: 14px; flex: none; }

  .footer-band { position: absolute; left: 0; bottom: 0; width: 744px; height: 18px; }

  .back-site {
    position: absolute;
    top: 338px;
    left: 0;
    width: 100%;
    text-align: center;
    font-size: 22px;
    letter-spacing: 3px;
  }
</style>
</head>
<body>
<main class="canvas">
  <section class="card card--front" aria-label="Business card front">
    <p class="holder"><span class="holder__name">Your name,</span> Title</p>
    <p class="wordmark">Corvane Freight</p>
    <address class="address">
      <span class="address__company">Corvane Freight.LLC</span><br>
      Street Name, City Name<br>
      State, City Zip Code
    </address>
    <div class="divider"></div>
    <ul class="contact">
      <li>
        <svg viewBox="0 0 16 16" aria-hidden="true"><circle cx="8" cy="8" r="7" fill="none" stroke="#fff" stroke-width="1.4"/><path d="M5 4.5c.6-.4 1.2 0 1.5.7l.4 1c.2.4 0 .8-.3 1l-.5.4c.5 1 1.2 1.7 2.2 2.2l.4-.5c.3-.3.7-.4 1-.3l1 .4c.6.3 1 .9.6 1.5-.6.9-1.6 1.2-2.6.7C7 10.7 5.3 9 4.4 7.1c-.4-1 0-2 .6-2.6z" fill="#fff"/></svg>
        123-456-7890
      </li>
      <li>
        <svg viewBox="0 0 16 16" aria-hidden="true"><circle cx="8" cy="8" r="6.5" fill="#fff"/><path d="M1.5 8h13M8 1.5c-2.5 3-2.5 10 0 13M8 1.5c2.5 3 2.5 10 0 13" fill="none" stroke="var(--card-blue)" stroke-width="1"/></svg>
        www.website.com
      </li>
      <li>ABN : 0123456789</li>
    </ul>
    <svg class="footer-band" viewBox="0 0 744 18" preserveAspectRatio="none" aria-hidden="true">
      <rect x="0" y="3" width="744" height="15" fill="var(--aqua)"/>
      <polygon points="368,3 392,3 380,18 356,18" fill="var(--card-blue-deep)"/>
      <polygon points="0,0 372,0 368,3 0,3" fill="var(--card-blue)"/>
    </svg>
  </section>

  <section class="card card--back" aria-label="Business card back">
    <p class="wordmark">Corvane Freight</p>
    <p class="back-site">www.website.com</p>
  </section>
</main>
</body>
</html>
```